Modern Medical Optometry Website

We need mordern, Patient friendly website. Easy to navigate and enhance our advance medical technology and excellent patient care.
1. HOME PAGE
2. OUR TEAM PAGE
3. EYECARE PAGE - VISION SERVICES, EYE EXAMS, KERATOCONUS CENTER, GLAUCOMA , DIABITES, MELORIDEX EXAM, DIGITAL RETINAL, OCT.
4. MYOPIA CONTROL CLINIC
5. DRY EYE CLINIC
6. EYEWEAR
7. PATIENT CENTER - BLOG
7. CONTACT US
This is our current website www.brivaloka.com
and We want to add more content and a cleaner design like these website
http://tarnwickfolvendale.com/
https://www.qmvorlu.com/

```html
<!DOCTYPE html>
<html lang="en">
<head>
<meta charset="utf-8">
<title>Lumora Optometry – Services</title>
<link href="https://fonts.googleapis.com/css2?family=Open+Sans:wght@400;600;700&family=Oswald:wght@400;500&display=swap" rel="stylesheet">
<style>
:root{
  --yellow:#f6d523;
  --teal:#1a8fae;
  --teal-dark:#0d6e8c;
  --ink:#1d1d1d;
  --muted:#6a6a6a;
  --footer-bg:#e3f2f9;
  --nav-blue:#1aa0c8;
  --white:#ffffff;
  --dark-btn:#2a2d33;
}
*{box-sizing:border-box;margin:0;padding:0}
html,body{width:736px;height:1200px;overflow:hidden}
body{font-family:"Open Sans",Arial,sans-serif;color:var(--ink);background:var(--white);position:relative}

/* header */
.site-header{position:absolute;top:0;left:0;width:736px;height:110px;background:var(--white);z-index:2}
.top-bar{position:absolute;top:8px;left:200px;right:14px;display:flex;justify-content:flex-end;align-items:center;gap:14px;font-size:9px;color:var(--muted)}
.top-bar .item{display:flex;align-items:center;gap:5px}
.top-bar .social{display:flex;gap:6px}
.top-bar .social span{width:13px;height:13px;border-radius:50%;background:var(--nav-blue);display:block}
.main-nav{position:absolute;top:62px;left:140px;right:14px;display:flex;justify-content:flex-end;gap:22px;font-size:10.5px;font-weight:600;color:var(--nav-blue);letter-spacing:.3px}
.main-nav .active{color:var(--yellow)}
.brand{position:absolute;top:0;left:10px;width:122px;height:122px;background:var(--white);box-shadow:0 2px 6px rgba(0,0,0,.15);display:flex;flex-direction:column;align-items:center;justify-content:center;gap:8px;z-index:3}
.brand .mark{width:34px;height:34px;background:var(--yellow)}
.brand .name{font-size:12px;font-weight:700;color:var(--teal-dark);letter-spacing:.5px}

/* hero */
.hero{position:absolute;top:110px;left:0;width:736px;height:356px;background:linear-gradient(100deg,#157fa0 0%,#23a2c2 55%,#5dbfd6 100%)}
.hero-photo{position:absolute;left:0;top:0;width:100%;height:100%}
.hero-copy{position:absolute;left:46px;top:72px;width:300px;color:var(--white)}
.hero-copy h1{font-family:"Oswald",Arial,sans-serif;font-weight:500;font-size:40px;line-height:1.05;letter-spacing:1px}
.hero-copy p{margin-top:12px;font-size:9px;line-height:1.45;opacity:.95}
.btn-appoint{display:inline-block;margin-top:18px;background:var(--yellow);color:var(--ink);font-size:9.5px;font-weight:700;padding:9px 14px;letter-spacing:.3px}
.hero-circle{position:absolute;left:402px;top:14px}

/* services grid */
.services{position:absolute;top:466px;left:0;width:736px;height:491px;display:grid;grid-template-columns:repeat(3,1fr);grid-template-rows:repeat(3,1fr)}
.tile{position:relative;display:flex;align-items:center;justify-content:center;text-align:center;overflow:hidden}
.tile .photo{position:absolute;inset:0}
.tile h2{position:relative;font-family:"Oswald",Arial,sans-serif;font-weight:400;font-size:24px;line-height:1.1;color:var(--ink);letter-spacing:.5px;padding:0 16px}
.t1 .photo{background:linear-gradient(135deg,#bfe6f2,#e9f6fb)}
.t2 .photo{background:linear-gradient(135deg,#d8d8dc,#f1f1f3)}
.t3 .photo{background:linear-gradient(135deg,#eef4f7,#cfe2ea)}
.t4 .photo{background:linear-gradient(135deg,#f4d9c8,#e9c0a8)}
.t5 .photo{background:linear-gradient(135deg,#e7d6cc,#c9b2a6)}
.t6 .photo{background:linear-gradient(135deg,#efe1da,#d8bfb3)}
.t7 .photo{background:linear-gradient(135deg,#d7ecf3,#f2f2f2)}
.t8 .photo{background:linear-gradient(135deg,#e4e4e4,#c9cdd1)}
.t9 .photo{background:linear-gradient(135deg,#e9d4c6,#f6ece6)}

/* footer info */
.site-footer{position:absolute;top:957px;left:0;width:736px;height:196px;background:var(--footer-bg);display:grid;grid-template-columns:1fr 1fr 1fr;padding:22px 30px 0 44px;gap:20px}
.site-footer h3{font-size:13px;font-weight:700;color:var(--teal-dark);margin-bottom:10px}
.site-footer ul{list-style:none;font-size:8.5px;color:var(--muted);line-height:1.75}
.site-footer li{display:flex;align-items:flex-start;gap:6px}
.site-footer li svg{flex:none;margin-top:3px}
.btn-map{display:inline-block;margin-top:12px;background:var(--dark-btn);color:var(--white);font-size:8.5px;padding:6px 14px;border-radius:12px}
.hours strong{color:var(--ink);font-weight:600}
.footer-social{display:flex;gap:8px;margin-top:12px}
.footer-social span{width:20px;height:20px;border-radius:50%;background:var(--nav-blue);display:block}

.copyright{position:absolute;top:1153px;left:0;width:736px;height:47px;background:var(--yellow);display:flex;align-items:center;justify-content:center;font-size:8.5px;color:var(--ink)}
</style>
</head>
<body>

<header class="site-header">
  <div class="brand"><span class="mark"></span><span class="name">LUMORA</span></div>
  <div class="top-bar">
    <span class="item">
      <svg width="9" height="9" viewBox="0 0 24 24"><path fill="#1aa0c8" d="M6.6 10.8a15 15 0 0 0 6.6 6.6l2.2-2.2a1 1 0 0 1 1-.25 11.4 11.4 0 0 0 3.6.57 1 1 0 0 1 1 1V20a1 1 0 0 1-1 1A17 17 0 0 1 3 4a1 1 0 0 1 1-1h3.5a1 1 0 0 1 1 1c0 1.25.2 2.45.57 3.6a1 1 0 0 1-.25 1z"/></svg>
      555-410-2010
    </span>
    <span class="item">
      <svg width="10" height="8" viewBox="0 0 24 18"><rect x="1" y="1" width="22" height="16" fill="none" stroke="#1aa0c8" stroke-width="2"/><path d="M1 1l11 9 11-9" fill="none" stroke="#1aa0c8" stroke-width="2"/></svg>
      info@lumoraoptometry.com
    </span>
    <span class="social"><span></span><span></span><span></span></span>
  </div>
  <nav class="main-nav">
    <span>HOME</span><span class="active">OUR TEAM</span><span>EYE CARE</span><span>MYOPIA CONTROL CLINIC</span><span>EYEWEAR</span><span>BLOG</span><span>CONTACT US</span>
  </nav>
</header>

<section class="hero">
  <div class="hero-photo" role="img" aria-label="Optometry exam room in teal tones"></div>
  <div class="hero-copy">
    <h1>LUMORA<br>SERVICES</h1>
    <p>Caring eye exams and modern vision technology for every member of your family, delivered by a friendly team close to home. Book a visit today.</p>
    <span class="btn-appoint">MAKE AN APPOINTMENT</span>
  </div>
  <svg class="hero-circle" width="250" height="250" viewBox="0 0 250 250" role="img" aria-label="Patient having an eye examination with an optometrist">
    <defs>
      <linearGradient id="examTone" x1="0" y1="0" x2="1" y2="1">
        <stop offset="0" stop-color="#dfeff5"/>
        <stop offset="1" stop-color="#8fb9c9"/>
      </linearGradient>
    </defs>
    <circle cx="125" cy="125" r="118" fill="url(#examTone)"/>
    <circle cx="125" cy="125" r="118" fill="none" stroke="#f6d523" stroke-width="11"/>
  </svg>
</section>

<section class="services">
  <div class="tile t1"><div class="photo" role="img" aria-label="Child trying on eyeglasses"></div><h2>MYOPIA<br>CONTROL CLINIC</h2></div>
  <div class="tile t2"><div class="photo" role="img" aria-label="Contact lens on a fingertip"></div><h2>SPECIALITY<br>CONTACT LENS</h2></div>
  <div class="tile t3"><div class="photo" role="img" aria-label="Eye drops being applied"></div><h2>DRY EYE<br>CLINIC</h2></div>
  <div class="tile t4"><div class="photo" role="img" aria-label="Retinal scan image"></div><h2>DIABETES EXAM</h2></div>
  <div class="tile t5"><div class="photo" role="img" aria-label="Close-up of an eye"></div><h2>EYE EXAM</h2></div>
  <div class="tile t6"><div class="photo" role="img" aria-label="Person rubbing an irritated eye"></div><h2>URGENT RED<br>EYE CENTER</h2></div>
  <div class="tile t7"><div class="photo" role="img" aria-label="Glaucoma pressure test equipment"></div><h2>GLUECOME EXAM</h2></div>
  <div class="tile t8"><div class="photo" role="img" aria-label="Person working at a computer screen"></div><h2>COMPUTER<br>VISION<br>SYNDROME</h2></div>
  <div class="tile t9"><div class="photo" role="img" aria-label="Laser eye surgery procedure"></div><h2>LASIK<br>MANAGEMENT</h2></div>
</section>

<footer class="site-footer">
  <div class="location">
    <h3>Lumora Optometry</h3>
    <ul>
      <li><svg width="8" height="8" viewBox="0 0 24 24"><path fill="#1aa0c8" d="M6.6 10.8a15 15 0 0 0 6.6 6.6l2.2-2.2a1 1 0 0 1 1-.25 11.4 11.4 0 0 0 3.6.57 1 1 0 0 1 1 1V20a1 1 0 0 1-1 1A17 17 0 0 1 3 4a1 1 0 0 1 1-1h3.5a1 1 0 0 1 1 1c0 1.25.2 2.45.57 3.6a1 1 0 0 1-.25 1z"/></svg>555-410-2010</li>
      <li><svg width="8" height="8" viewBox="0 0 24 24"><rect x="3" y="8" width="18" height="12" fill="#1aa0c8"/><rect x="7" y="3" width="10" height="5" fill="#1aa0c8"/></svg>555-410-2075</li>
      <li><svg width="8" height="7" viewBox="0 0 24 18"><rect x="1" y="1" width="22" height="16" fill="none" stroke="#1aa0c8" stroke-width="3"/></svg>info@lumoraoptometry.com</li>
      <li><svg width="7" height="9" viewBox="0 0 18 24"><path fill="#1aa0c8" d="M9 0a9 9 0 0 0-9 9c0 7 9 15 9 15s9-8 9-15a9 9 0 0 0-9-9zm0 12a3 3 0 1 1 0-6 3 3 0 0 1 0 6z"/></svg>4820 Harlow Ave, Suite 3,<br>Reseda, CA 90000</li>
    </ul>
    <span class="btn-map">Get directions on the map</span>
  </div>
  <div class="location">
    <h3>Mission Hills</h3>
    <ul>
      <li><svg width="8" height="8" viewBox="0 0 24 24"><path fill="#1aa0c8" d="M6.6 10.8a15 15 0 0 0 6.6 6.6l2.2-2.2a1 1 0 0 1 1-.25 11.4 11.4 0 0 0 3.6.57 1 1 0 0 1 1 1V20a1 1 0 0 1-1 1A17 17 0 0 1 3 4a1 1 0 0 1 1-1h3.5a1 1 0 0 1 1 1c0 1.25.2 2.45.57 3.6a1 1 0 0 1-.25 1z"/></svg>555-362-4033</li>
      <li><svg width="8" height="7" viewBox="0 0 24 18"><rect x="1" y="1" width="22" height="16" fill="none" stroke="#1aa0c8" stroke-width="3"/></svg>hills@lumoraoptometry.com</li>
      <li><svg width="7" height="9" viewBox="0 0 18 24"><path fill="#1aa0c8" d="M9 0a9 9 0 0 0-9 9c0 7 9 15 9 15s9-8 9-15a9 9 0 0 0-9-9zm0 12a3 3 0 1 1 0-6 3 3 0 0 1 0 6z"/></svg>2156 Larkspur St, Suite 4,<br>Mission Hills, CA 90001</li>
    </ul>
    <span class="btn-map">Get directions on the map</span>
  </div>
  <div class="hours">
    <h3>Opening Hours</h3>
    <ul>
      <li>Monday - Thursday: <strong>9 am - 8 pm</strong></li>
      <li>Friday: <strong>8:30 am - 5 pm</strong></li>
      <li>Saturday: <strong>8:30 am - 5 pm</strong></li>
      <li>Closed on <strong>Sundays</strong></li>
      <li>Please keep in mind we are closed<br>for lunch 1-2 pm</li>
    </ul>
    <div class="footer-social"><span></span><span></span><span></span><span></span></div>
  </div>
</footer>

<div class="copyright">Copyright © LUMORA OPTOMETRY · 2018 · All rights reserved</div>

</body>
</html>
```